Blue Harbor Inc - Cutting-Edge Biotech Laboratory - Sleek & Sophisticated

Please design a website that has more of a high-tech and high-end feel, with contents outlined in the uploaded file.

Please have main tabs of the following categories: Home, About, FDA & LAWS, Science, Products, Media, Contact.

Media can include all the videos and photos.

Current website: www.blueharborlabs.com - it needs to be much more high-end, sleek and more organized. Please do NOT follow the outlines in the old website, but follow the uploaded CONTENT file.

Target Market(s)

doctors

Industry/Entity Type

Biotechnology

Coding

Coded - Design and coding required

Number of Pages Required

5+ page

Requirements
Must have
• Logo
Nice to have
• Some lotion on the website

```html
<!DOCTYPE html>
<html lang="en">
<head>
<meta charset="utf-8">
<title>Blue Harbor Inc</title>
<link rel="stylesheet" href="https://fonts.googleapis.com/css2?family=Cinzel:wght@400;600;700&family=Montserrat:wght@500;600&family=Open+Sans:wght@400;600&display=swap">
<style>
:root{
  --blue:#0d4fb3;
  --blue-deep:#0a3c8c;
  --ink:#2b2b2b;
  --muted:#555;
  --white:#fff;
  --light:#f1f1f1;
  --rule:#c9c9c9;
}
*{margin:0;padding:0;box-sizing:border-box}
html,body{width:1200px;height:3529px;overflow:hidden;background:var(--white)}
body{position:relative;font-family:"Open Sans",Arial,sans-serif;color:var(--ink)}
.abs{position:absolute}
.serif{font-family:"Cinzel",Georgia,serif}
.center{left:0;width:1200px;text-align:center}

/* header + hero */
.hero{top:0;left:0;width:1200px;height:588px;background:radial-gradient(circle at 22% 40%,#3f7fd6 0,#1a55b8 18%,transparent 30%),radial-gradient(circle at 78% 60%,#8fb6e8 0,#4f86d2 20%,transparent 38%),linear-gradient(160deg,#0c3f9e 0%,#2a6bcc 45%,#a9c8ee 75%,#1b56b8 100%)}
.logo{top:28px;left:56px;font-family:"Cinzel",Georgia,serif;font-size:30px;font-weight:600;color:var(--white);letter-spacing:1px}
.main-nav{top:38px;right:76px;display:flex;gap:34px}
.main-nav a{font-family:"Cinzel",Georgia,serif;font-size:13.5px;color:var(--white);text-decoration:none;font-weight:600}
.hero-title{top:296px;font-size:32px;line-height:38px;color:var(--white);font-weight:600;letter-spacing:1px}
.dots{top:524px;left:565px;display:flex;gap:12px}
.dots span{width:9px;height:9px;border-radius:50%;background:rgba(255,255,255,.75)}
.dots span:first-child{background:var(--blue)}

/* video */
.video{top:588px;left:0;width:1200px;height:476px;background:linear-gradient(90deg,#2e2418 0%,#5a4630 30%,#6c5a46 50%,#4a3a28 75%,#241c12 100%)}
.play{top:688px;left:544px}
.video-kicker{top:830px;font-size:14px;color:var(--white);letter-spacing:1px}
.video-title{top:852px;font-size:42px;color:var(--white);font-weight:600}
.btn{display:block;width:202px;height:44px;line-height:44px;border-radius:22px;text-align:center;font-family:"Cinzel",Georgia,serif;font-size:15px;font-weight:600;text-decoration:none}
.btn-light{background:var(--white);color:var(--ink)}
.btn-blue{background:var(--blue);color:var(--white)}
.btn-outline{border:2px solid var(--ink);color:var(--ink);width:142px;height:38px;line-height:34px;font-size:12px}
.btn-small{width:142px;height:38px;line-height:38px;font-size:12px}

/* headings */
.section-title{font-family:"Cinzel",Georgia,serif;font-size:44px;font-weight:700;color:var(--blue);letter-spacing:1px}

/* about */
.about-text{top:1218px;left:85px;width:1030px;text-align:center;font-size:14.5px;line-height:26px;color:var(--muted)}
.rule{top:1471px;left:301px;width:680px;height:1px;background:var(--rule)}
.spec{top:1534px;width:180px;height:180px;border-radius:50%;background:var(--white);box-shadow:0 8px 22px rgba(0,0,0,.12);text-align:center}
.spec svg{margin-top:42px}
.spec p{font-family:"Montserrat",Arial,sans-serif;font-size:14px;font-weight:500;margin-top:10px;color:var(--ink)}
.spec.active{background:var(--blue)}
.spec.active p{color:var(--white)}

/* team */
.team-bg{top:1781px;left:0;width:1200px;height:998px;background:radial-gradient(circle at 30% 40%,#9a9a9a 0,#5c5c5c 30%,#2a2a2a 70%),#3a3a3a}
.team-panel{top:1908px;left:132px;width:936px;height:737px;background:var(--white)}
.member{width:280px;text-align:center}
.avatar{width:164px;height:164px;border-radius:50%;margin:0 auto;background:linear-gradient(160deg,#d9d9d9,#9c9c9c)}
.member h3{font-family:"Montserrat",Arial,sans-serif;font-size:17px;font-weight:600;margin-top:20px;color:var(--ink)}
.member p{font-size:13px;line-height:28px;color:var(--muted)}

/* research */
.research-text{top:2936px;left:60px;width:1080px;text-align:center;font-size:14px;line-height:27px;color:var(--muted)}
.card{top:3054px;width:337px;height:229px;padding:34px 26px}
.card h4{font-size:14px;line-height:22px;font-weight:400;height:104px}
.card-blue{background:linear-gradient(135deg,#0d3f9a,#2a63c4 60%,#0b3480)}
.card-blue h4{color:var(--white)}
.card-grey{background:linear-gradient(135deg,#f4f4f4,#c9c9c9 60%,#e8e8e8)}
.card-grey h4{color:var(--ink)}

/* footer */
.footer{top:3341px;left:0;width:1200px;height:188px;background:var(--light)}
.footer-logo{top:3390px;font-size:30px;font-weight:600;color:var(--ink);letter-spacing:1px}
.footer-nav{top:3455px;left:0;width:1200px;display:flex;justify-content:center;gap:40px}
.footer-nav a{font-family:"Cinzel",Georgia,serif;font-size:13px;color:var(--ink);text-decoration:none}
.copyright{top:3490px;font-family:"Cinzel",Georgia,serif;font-size:12px;color:var(--ink)}
</style>
</head>
<body>

<div class="abs hero" role="img" aria-label="Blue microscopic view of stem cells"></div>
<div class="abs logo">BLUE HARBOR</div>
<nav class="abs main-nav">
  <a href="#">HOME</a><a href="#">ABOUT</a><a href="#">FDA &amp; LAWS</a><a href="#">SCIENCE</a><a href="#">PRODUCTS</a><a href="#">CONTACT</a>
</nav>
<h1 class="abs center hero-title serif">LEADER IN REGENERATIVE MEDICINE<br>INNOVATOR OF THE INDUSTRY</h1>
<div class="abs dots"><span></span><span></span><span></span><span></span></div>

<section>
  <div class="abs video" role="img" aria-label="Two people seated in armchairs during an interview"></div>
  <svg class="abs play" width="112" height="112" viewBox="0 0 112 112">
    <circle cx="56" cy="56" r="52" fill="none" stroke="#0d4fb3" stroke-width="5"/>
    <path d="M42 32 L82 56 L42 80 Z" fill="#0d4fb3"/>
  </svg>
  <p class="abs center video-kicker serif">INTERVIEW WITH BLUE HARBOR CHIEF SCIENTIST</p>
  <h2 class="abs center video-title serif">MARCO DELGADO ON STEM CELLS</h2>
  <a class="abs btn btn-light" style="top:916px;left:499px" href="#">WATCH NOW</a>
</section>

<section>
  <h2 class="abs center section-title" style="top:1124px">ABOUT</h2>
  <p class="abs about-text">Blue Harbor Therapy provides Non-Embryonic Stem Cells and unique protocols to doctors in order to help their patients who face major health conditions, as well as those who simply wish to stay young and healthy. Over the past seven years of development, we have successfully conducted research into major diseases related to kidney, liver and heart failures, and have aided in helping people who have suffered stroke or brain injury to walk or talk again. We have helped to remove all traces of tumor in multiple cancer patients and have achieved notable results in fighting aging and its physical markers.</p>
  <a class="abs btn btn-blue" style="top:1352px;left:499px" href="#">READ MORE</a>
  <div class="abs rule"></div>

  <div class="abs spec active" style="left:62px">
    <svg width="66" height="66" viewBox="0 0 66 66" fill="none" stroke="#fff" stroke-width="2.5"><circle cx="33" cy="33" r="30"/><circle cx="33" cy="20" r="7"/><path d="M22 50 L28 30 L38 30 L44 50"/></svg>
    <p>Orthopedics</p>
  </div>
  <div class="abs spec" style="left:284px">
    <svg width="66" height="66" viewBox="0 0 66 66" fill="none" stroke="#222" stroke-width="2.5"><rect x="22" y="8" width="22" height="8"/><rect x="20" y="16" width="26" height="42" rx="3"/><path d="M20 30 H46 M20 44 H46"/></svg>
    <p>Sports Medicine</p>
  </div>
  <div class="abs spec" style="left:508px">
    <svg width="66" height="66" viewBox="0 0 66 66" fill="none" stroke="#222" stroke-width="2.5"><circle cx="33" cy="33" r="30"/><path d="M14 44 L50 20 M18 50 L54 26"/></svg>
    <p>Wound Care</p>
  </div>
  <div class="abs spec" style="left:731px">
    <svg width="66" height="66" viewBox="0 0 66 66" fill="none" stroke="#222" stroke-width="2.5"><path d="M26 6 H40 V40 L56 48 V58 H20 V40 Z"/></svg>
    <p>Podiatry</p>
  </div>
  <div class="abs spec" style="left:952px">
    <svg width="66" height="66" viewBox="0 0 66 66" fill="none" stroke="#222" stroke-width="2.5"><circle cx="33" cy="33" r="30"/><path d="M24 12 V54 M33 10 V56 M42 12 V54 M14 22 L52 46"/></svg>
    <p>Pain Management</p>
  </div>
</section>

<section>
  <div class="abs team-bg" role="img" aria-label="Grayscale microscopic cell texture"></div>
  <div class="abs team-panel"></div>
  <h2 class="abs center section-title" style="top:1948px">TEAM</h2>

  <div class="abs member" style="top:2052px;left:196px"><div class="avatar" role="img" aria-label="Portrait of Marco Delgado"></div><h3>Marco Delgado</h3><p>Chief Scientist</p></div>
  <div class="abs member" style="top:2052px;left:474px"><div class="avatar" role="img" aria-label="Portrait of Laura Whitfield"></div><h3>Laura Whitfield</h3><p>Stem Cell Projects</p></div>
  <div class="abs member" style="top:2052px;left:733px"><div class="avatar" role="img" aria-label="Portrait of Dr. Peter L. Ames"></div><h3>Dr. Peter L. Ames</h3><p>Ames Center for Cardiac Longevity</p></div>

  <div class="abs member" style="top:2335px;left:196px"><div class="avatar" role="img" aria-label="Portrait of Dr. Owen Hartley"></div><h3>Dr. Owen Hartley</h3><p>1420 Meadow Park Dr #B,<br>Cedar Falls TX 77000</p></div>
  <div class="abs member" style="top:2335px;left:474px"><div class="avatar" role="img" aria-label="Portrait of Dr. Simon Brakeman"></div><h3>Dr. Simon Brakeman</h3><p>3150 Lakeview Rd #210,<br>Fairhaven MI 48000</p></div>
  <div class="abs member" style="top:2335px;left:733px"><div class="avatar" role="img" aria-label="Portrait of Dr. Nathan R. Cole"></div><h3>Dr. Nathan R. Cole</h3><p>Prime Vascular Services - 2210<br>Elm Ln #305, Riverton TX 75000</p></div>
</section>

<section>
  <h2 class="abs center section-title" style="top:2863px">RESEARCH</h2>
  <p class="abs research-text">Blue Harbor Inc in keenly interested in stem cell research, in areas of both laboratory and clinical studies. We strive to in understand the multitude of uses of stem cells and the ideal parameters of such usage. Contact us about possible research partnerships.</p>

  <article class="abs card card-blue" style="left:68px" role="img" aria-label="Blue cell imagery behind research article">
    <h4>Biliary tree stem cells, precursors to pancreatic committed progenitors: Evidence for possible life-long pancreatic organogenesis</h4>
    <a class="btn btn-light btn-small" href="#">READ MORE</a>
  </article>
  <article class="abs card card-grey" style="left:433px" role="img" aria-label="Laboratory pipette imagery behind research article">
    <h4>BMP-7 Induces Adult Human Pancreatic Exocrine-to-Endocrine</h4>
    <a class="btn btn-outline" href="#">READ MORE</a>
  </article>
  <article class="abs card card-grey" style="left:798px" role="img" aria-label="Grey cell imagery behind research article">
    <h4>Concise Review: Mesenchymal Stem Cells for Diabetes</h4>
    <a class="btn btn-outline" href="#">READ MORE</a>
  </article>
</section>

<footer>
  <div class="abs footer"></div>
  <div class="abs center footer-logo serif">BLUE HARBOR</div>
  <nav class="abs footer-nav">
    <a href="#">HOME</a><a href="#">ABOUT</a><a href="#">FDA &amp; LAWS</a><a href="#">SCIENCE</a><a href="#">PRODUCTS</a><a href="#">CONTACT</a>
  </nav>
  <p class="abs center copyright">© 2018 COMPANY NAME | ALL RIGHTS RESERVED</p>
</footer>

</body>
</html>
```